BrivoTerna. Lantern of the Steady Harvest. Business card

Professional business card for BrivoTerna (Lantern of the Steady Harvest)
My rationale: Strategy-> Execution-> Results-> Value that lead to the BrivoTerna name: We put the Lantern of the Steady Harvest.
We deliver value to our customers helping them at defining a good strategy (cyan arrow). 90% of well formulated strategies fail due to poor execution so we also consider strategical execution very important (green arrow). Due to the execution we obtain the results (blue arrow). Finally, the results provide feedback to redefine strategy, and the new strategy has to be executed and new results obtained providing new feedback and on and on. It's like a wheel that finally, must create corporate value: value for shareholders, staholders, employees, providers...-

Target Market(s)

CEOs and steering comitees , invewrnent funds

Industry/Entity Type

Business Consultant

Contact Information for Business Card

Teodoro Vinsquel
CEO & Founder
teodoro.vinsquel@brivoterna-example.com
Mobile: +34 655.803.912
www.brivoterna-example.com

Colors

Designer to choose colors to be used in the design.

Requirements
Nice to have
• Nice to hace the words: Strategy, execution, results
• Nice to vave the claim: Lantern of the Steady Harvest
• The three colors should be shown:
• cyan for STRATEGY
• green for EXECUTION
• blue for RESULTS
Should not have
• Complete black background

```html
<!DOCTYPE html>
<html lang="en">
<head>
<meta charset="utf-8">
<title>BrivoTerna — Business Card</title>
<link rel="stylesheet" href="https://fonts.googleapis.com/css2?family=Open+Sans:wght@400;600;700&display=swap">
<style>
  :root {
    --stage: #45474b;
    --card-blue: #233f96;
    --strategy-cyan: #27ade3;
    --execution-green: #97c93d;
    --paper: #ffffff;
    --ink-white: #ffffff;
  }
  * { box-sizing: border-box; margin: 0; padding: 0; }
  html, body {
    width: 1200px; height: 900px; overflow: hidden;
    background: var(--stage);
    font-family: "Open Sans", Arial, sans-serif;
  }
  .canvas { position: relative; width: 1200px; height: 900px; }
  .card {
    position: absolute; width: 600px; height: 343px;
    border-radius: 16px; overflow: hidden;
    box-shadow: 0 18px 40px rgba(0,0,0,0.35);
  }
  .card-back { left: 40px; top: 60px; background: var(--card-blue); }
  .card-front { left: 570px; top: 510px; background: var(--card-blue); }

  .wordmark {
    display: flex; align-items: center; gap: 10px;
    font-weight: 700; letter-spacing: -0.5px; white-space: nowrap;
  }
  .wordmark-dot { border-radius: 50%; flex: none; }

  .card-back .wordmark {
    position: absolute; left: 0; right: 0; top: 138px;
    justify-content: center; color: var(--ink-white); font-size: 46px;
  }
  .card-back .wordmark-dot { width: 22px; height: 22px; background: var(--ink-white); }
  .card-back .web {
    position: absolute; right: 30px; bottom: 28px;
    color: var(--ink-white); font-size: 14px; letter-spacing: 0.3px;
  }

  .front-bands { position: absolute; inset: 0; width: 100%; height: 100%; }
  .card-front .wordmark {
    position: absolute; left: 26px; top: 186px;
    color: var(--card-blue); font-size: 30px;
  }
  .card-front .wordmark-dot { width: 14px; height: 14px; background: var(--card-blue); }

  .identity {
    position: absolute; right: 30px; top: 38px; text-align: right;
  }
  .identity .person { color: var(--ink-white); font-weight: 700; font-size: 21px; white-space: nowrap; }
  .identity .role { color: var(--strategy-cyan); font-size: 15px; margin-top: 1px; }
  .identity .rule {
    width: 56px; height: 3px; background: var(--execution-green);
    margin: 6px 0 0 auto;
  }

  .contacts {
    position: absolute; right: 22px; top: 150px;
    list-style: none; display: flex; flex-direction: column; gap: 10px;
  }
  .contact {
    display: flex; align-items: center; justify-content: flex-end; gap: 8px;
    color: var(--ink-white); font-size: 12px; white-space: nowrap;
  }
  .contact-icon {
    width: 26px; height: 26px; border-radius: 50%;
    background: var(--paper); display: flex; align-items: center; justify-content: center;
    flex: none;
  }
  .contact-icon svg { width: 14px; height: 14px; }
</style>
</head>
<body>
<main class="canvas">

  <section class="card card-back" aria-label="Card back">
    <div class="wordmark"><span class="wordmark-dot"></span><span>BrivoTerna</span></div>
    <p class="web">www.brivoterna-example.com</p>
  </section>

  <section class="card card-front" aria-label="Card front">
    <svg class="front-bands" viewBox="0 0 600 343" preserveAspectRatio="none" aria-hidden="true">
      <path d="M215,0 L345,0 Q265,120 262,343 Q265,90 215,0 Z" fill="var(--execution-green)"/>
      <path d="M130,0 L215,0 Q265,90 262,343 Q250,40 130,0 Z" fill="var(--strategy-cyan)"/>
      <path d="M0,0 L130,0 Q250,40 255,343 L0,343 Z" fill="var(--paper)"/>
    </svg>

    <div class="wordmark"><span class="wordmark-dot"></span><span>BrivoTerna</span></div>

    <div class="identity">
      <p class="person">Teodoro Vinsquel</p>
      <p class="role">CEO &amp; Founder</p>
      <div class="rule"></div>
    </div>

    <ul class="contacts">
      <li class="contact">
        <span>+34 655.803.912</span>
        <span class="contact-icon">
          <svg viewBox="0 0 14 14"><rect x="3.5" y="1" width="7" height="12" rx="1.5" fill="none" stroke="#233f96" stroke-width="1.6"/><circle cx="7" cy="10.6" r="0.9" fill="#233f96"/></svg>
        </span>
      </li>
      <li class="contact">
        <span>www.brivoterna-example.com</span>
        <span class="contact-icon">
          <svg viewBox="0 0 14 14"><circle cx="7" cy="7" r="5.5" fill="#233f96"/><path d="M1.5,7 H12.5 M7,1.5 V12.5 M3,4 H11 M3,10 H11" stroke="#fff" stroke-width="0.7" fill="none"/></svg>
        </span>
      </li>
      <li class="contact">
        <span>teodoro.vinsquel@brivoterna-example.com</span>
        <span class="contact-icon">
          <svg viewBox="0 0 14 14"><path d="M12.5,1.5 L1.5,6.5 L6,8 L7.5,12.5 Z" fill="#233f96"/></svg>
        </span>
      </li>
    </ul>
  </section>

</main>
</body>
</html>
```